Maple Roster Business Card for recruitment company

We are looking for a Business Card Design that incorporates our personal details and our busines name and logo. We are a specialized search consultancy that recruit Property and Construction professionals.
We would like a business card that stands out and is appealing to the Construction and Property industry as well.

Target Market(s)

people in the construction and property industry

Contact Information for Business Card

Business Name and logo

Font styles to use
Serif

Colors
0094D4
00A9DD
6FCCEA
C7EBF8
E9F6FB

Requirements
Must have
• Business name and logo as well as contact details
Should not have
• No photos of us please

```html
<!DOCTYPE html>
<html lang="en">
<head>
<meta charset="utf-8">
<title>Maple Roster – Business Card</title>
<link rel="stylesheet" href="https://fonts.googleapis.com/css2?family=Montserrat:wght@400;600&display=swap">
<style>
  :root {
    --bg: #3b3b3b;
    --teal: #0c4a5e;
    --teal-deep: #083b4c;
    --sky: #00a9dd;
    --ink: #0c4a5e;
    --muted: #5d6b72;
    --paper: #ffffff;
  }
  * { margin: 0; padding: 0; box-sizing: border-box; }
  html, body { width: 1200px; height: 900px; overflow: hidden; }
  body {
    background: radial-gradient(circle at 50% 40%, #4a4a4a 0%, var(--bg) 70%);
    font-family: "Montserrat", sans-serif;
    position: relative;
  }
  .card {
    position: absolute;
    border-radius: 18px;
    overflow: hidden;
    box-shadow: 0 18px 40px rgba(0,0,0,0.45);
  }

  /* Front: vertical card */
  .card-front {
    left: 150px; top: 140px;
    width: 360px; height: 620px;
    background: var(--paper);
  }
  .front-band {
    height: 300px;
    background: var(--teal);
    display: flex;
    align-items: center;
    justify-content: center;
    gap: 14px;
  }
  .brand-dot {
    width: 22px; height: 22px;
    border-radius: 50%;
    background: var(--paper);
  }
  .brand-name {
    color: var(--paper);
    font-weight: 600;
    font-size: 30px;
    letter-spacing: 3px;
    text-transform: uppercase;
  }
  .front-body { padding: 48px 36px 0; }
  .person-name {
    color: var(--ink);
    font-weight: 600;
    font-size: 30px;
    letter-spacing: 2px;
    text-transform: uppercase;
  }
  .person-role {
    color: var(--muted);
    font-size: 15px;
    letter-spacing: 2px;
    text-transform: uppercase;
    margin-top: 2px;
  }
  .contact-list {
    margin-top: 30px;
    display: grid;
    grid-template-columns: 84px 1fr;
    row-gap: 8px;
    font-size: 15px;
  }
  .contact-label { color: var(--ink); }
  .contact-value { color: var(--muted); }

  /* Back: horizontal card */
  .card-back {
    left: 570px; top: 180px;
    width: 520px; height: 320px;
    background: linear-gradient(135deg, var(--teal) 0%, var(--teal-deep) 100%);
    display: flex;
    align-items: center;
    justify-content: center;
  }
  .back-name {
    color: var(--sky);
    font-weight: 400;
    font-size: 46px;
    letter-spacing: 6px;
    text-transform: uppercase;
  }
</style>
</head>
<body>
  <section class="card card-front">
    <div class="front-band">
      <span class="brand-dot"></span>
      <span class="brand-name">Maple Roster</span>
    </div>
    <div class="front-body">
      <h1 class="person-name">Daniel Hart</h1>
      <p class="person-role">Founder</p>
      <dl class="contact-list">
        <dt class="contact-label">Phone</dt><dd class="contact-value">: +64 21 480 2297</dd>
        <dt class="contact-label">Email</dt><dd class="contact-value">: daniel@mapleroster.nz</dd>
        <dt class="contact-label">Web</dt><dd class="contact-value">: www.mapleroster.nz</dd>
        <dt class="contact-label">Address</dt><dd class="contact-value">: Kestrel Bay, New Zealand</dd>
      </dl>
    </div>
  </section>

  <section class="card card-back">
    <span class="back-name">Maple Roster</span>
  </section>
</body>
</html>
```